Sparrow Haulage needs a business card design.

Design a double-sided business card for new freight business. On the front, would like to see our logo along with the following info:

Martin Obuya
CEO/FOUNDER
555-206-7142
martinobuya@sparrow-haulage.example

On the reverse side, we would like to use the graphic image of our logo only without the Sparrow Haulage name.

```html
<!DOCTYPE html>
<html lang="en">
<head>
<meta charset="UTF-8">
<title>Sparrow Haulage – Business Card</title>
<link rel="stylesheet" href="https://fonts.googleapis.com/css2?family=Montserrat:wght@500;700;800&display=swap">
<style>
  :root {
    --stage: #2e2e30;
    --navy: #0d1460;
    --red: #c8101a;
    --ink: #333338;
    --white: #ffffff;
    --grad-top: #c40d12;
    --grad-mid: #6a0a3e;
    --grad-bottom: #0b0c5a;
  }
  * { box-sizing: border-box; margin: 0; padding: 0; }
  html, body {
    width: 1200px; height: 1015px; overflow: hidden;
    background: var(--stage);
    font-family: "Montserrat", Arial, sans-serif;
  }
  .stage {
    width: 1200px; height: 1015px;
    display: flex; flex-direction: column; align-items: center; justify-content: center;
    gap: 44px;
  }
  .card {
    width: 760px; height: 434px;
    position: relative; overflow: hidden;
    box-shadow: 0 12px 30px rgba(0,0,0,.55);
  }

  /* Reverse side: brand pattern area with a single plain mark */
  .card-back {
    display: flex; align-items: center; justify-content: center;
  }
  .back-pattern {
    position: absolute; inset: 0;
    background: linear-gradient(160deg, var(--grad-top) 0%, var(--grad-mid) 50%, var(--grad-bottom) 100%);
  }
  .back-mark {
    position: relative;
    width: 52px; height: 52px;
    background: var(--white);
  }

  /* Front side */
  .card-front { background: var(--white); }
  .brand {
    position: absolute; left: 72px; top: 120px;
    display: flex; align-items: center; gap: 18px;
  }
  .brand-mark { width: 30px; height: 30px; background: var(--red); flex: none; }
  .brand-name {
    color: var(--navy);
    font-weight: 800; font-size: 34px; letter-spacing: 5px;
    text-transform: uppercase; line-height: 1; white-space: nowrap;
  }
  .person {
    position: absolute; left: 250px; top: 200px;
  }
  .person-name {
    font-weight: 800; font-size: 27px; letter-spacing: 1px;
    text-transform: uppercase; color: var(--navy); line-height: 1.2;
  }
  .person-name .surname { color: var(--red); }
  .person-role {
    font-weight: 500; font-size: 19px; color: var(--ink);
    letter-spacing: 1px; margin-top: 2px;
  }
  .contacts {
    list-style: none; margin-top: 30px;
    display: flex; flex-direction: column; gap: 9px;
  }
  .contacts li {
    display: flex; align-items: center; gap: 12px;
    font-weight: 500; font-size: 17px; color: var(--ink); white-space: nowrap;
  }
  .contacts svg { width: 18px; height: 18px; flex: none; }
  .web-accent-navy { color: var(--navy); }
  .web-accent-red { color: var(--red); }
</style>
</head>
<body>
<main class="stage">
  <section class="card card-back" aria-label="Business card reverse">
    <div class="back-pattern" role="img" aria-label="Repeating brand pattern over a red to navy gradient"></div>
    <span class="back-mark" aria-hidden="true"></span>
  </section>

  <section class="card card-front" aria-label="Business card front">
    <div class="brand">
      <span class="brand-mark"></span>
      <span class="brand-name">Sparrow Haulage</span>
    </div>

    <div class="person">
      <p class="person-name">Martin <span class="surname">Obuya</span></p>
      <p class="person-role">CEO/FOUNDER</p>
      <ul class="contacts">
        <li>
          <svg viewBox="0 0 24 24" aria-hidden="true"><path fill="#c8101a" d="M6.6 10.8a15 15 0 0 0 6.6 6.6l2.2-2.2a1 1 0 0 1 1-.25 11.4 11.4 0 0 0 3.6.57 1 1 0 0 1 1 1V20a1 1 0 0 1-1 1A17 17 0 0 1 3 4a1 1 0 0 1 1-1h3.5a1 1 0 0 1 1 1c0 1.25.2 2.45.57 3.6a1 1 0 0 1-.25 1z"/></svg>
          555-206-7142
        </li>
        <li>
          <svg viewBox="0 0 24 24" aria-hidden="true"><rect x="2" y="5" width="20" height="14" fill="#c8101a"/><path d="M2 5l10 8 10-8" fill="none" stroke="#fff" stroke-width="1.6"/></svg>
          martinobuya@sparrow-haulage.example
        </li>
        <li>
          <svg viewBox="0 0 24 24" aria-hidden="true"><g fill="none" stroke="#c8101a" stroke-width="2"><circle cx="12" cy="12" r="9.5"/><ellipse cx="12" cy="12" rx="4" ry="9.5"/><path d="M2.5 12h19M4 7h16M4 17h16"/></g></svg>
          <span>www.<span class="web-accent-navy">sparrow-</span><span class="web-accent-red">haulage</span>.example</span>
        </li>
      </ul>
    </div>
  </section>
</main>
</body>
</html>
```